Christian Media Company Website

I am looking to design an easy to follow, sleek, creative website for my Christian video Bible study platform. On this platform you will be able to sign up to have access to dozens of free high-quality video Bible studies. With that being said There will be a total of 3 pages needed.

First, I will need the home page. This should contain all critical information to inform the customer. The design should be easy to follow, professional, and creative. I will post to some websites I like, if you just copy the website in your design will be removed immediately.

Secondly, we will need a landing Bible study page for people to look through the Bible studies to select one. I have uploaded Study images below with the aspect ratio I want for the design (for each Bible study image). There should be 2 sections Topical studies and Doctrinal Studies (with series under each section). I would like for people to be able to slide left or right through the studies under each category.

Lastly, we will need a video series page. This page needs to have the video they are watching, a playlist of the other videos, as well as a place to put the speaker's image and description. We will have studies that they can download so please make a place for this.

I will upload our color in the files along with our logo! Looking forward to seeing what you all will come up with!

Websites I like :
https://lanternvale.org/
https://www.quillharborfilms.org/
https://www.dunmorel.com/
https://tessavint.org/

Target Market(s)

Christians

Industry/Entity Type

Christian Video Design

Coding

Coded - Design and coding required

Number of Pages Required

3 page

Font styles to use
Sans Serif

Colors
00AB8E
00BBA5
67D7C9
C6EFE9
E9F9F6

Requirements
Should not have
• Pre-Used Templates

```html
<!DOCTYPE html>
<html lang="en">
<head>
<meta charset="utf-8">
<title>Gathered Path – Christian Bible Study Platform</title>
<link href="https://fonts.googleapis.com/css2?family=Poppins:wght@300;400;500;600;700&display=swap" rel="stylesheet">
<style>
:root{
  --green:#00AB8E;
  --teal:#00BBA5;
  --mint:#67D7C9;
  --pale:#C6EFE9;
  --wash:#E9F9F6;
  --ink:#1d1d1d;
  --grey:#555;
  --white:#fff;
}
*{box-sizing:border-box;margin:0;padding:0}
html,body{width:1200px;height:2818px;overflow:hidden;background:var(--white);font-family:'Poppins',sans-serif;color:var(--ink)}
.page{position:relative;width:1200px;height:2818px;overflow:hidden}
.abs{position:absolute}
a{color:inherit;text-decoration:none}

/* hero */
.hero-photo{position:absolute;left:0;top:0;width:1200px;height:570px;background:linear-gradient(160deg,#f6e3e6 0%,#f1d2d6 30%,#e9c3b4 65%,#c99b7d 100%);clip-path:polygon(0 0,1200px 0,1200px 545px,620px 569px,0 545px)}
.hero-shape{position:absolute;left:0;top:0;width:620px;height:570px}
.topmail{left:112px;top:15px;color:var(--white);font-size:15px;font-weight:500;display:flex;align-items:center;gap:12px}
.socials{right:112px;top:17px;display:flex;gap:10px}
.socials span{width:22px;height:22px;border:2px solid var(--green);border-radius:50%;display:block}
.navbar{left:109px;top:54px;width:979px;height:85px;background:var(--white);border-radius:10px;box-shadow:0 2px 10px rgba(0,0,0,.06)}
.brand{position:absolute;left:106px;top:15px;color:var(--green);font-weight:600;font-size:20px;line-height:27px}
.menu{position:absolute;left:273px;top:0;height:85px;display:flex;align-items:center;gap:32px;font-size:17px;font-weight:500}
.menu .active{color:var(--green);position:relative}
.menu .active::before{content:"";position:absolute;left:0;right:0;top:-31px;height:3px;background:var(--mint)}
.signup{position:absolute;right:18px;top:20px;width:141px;height:45px;background:var(--green);color:var(--white);border-radius:23px;font-size:17px;display:flex;align-items:center;justify-content:center}
.hero-title{left:110px;top:226px;color:var(--white)}
.hero-title .lead{font-size:53px;font-weight:400;line-height:60px}
.hero-title .big{font-size:57px;font-weight:700;line-height:62px;margin-top:4px}
.cta{left:112px;top:450px;width:179px;height:53px;background:var(--white);color:var(--green);border-radius:9px;font-weight:500;font-size:17px;display:flex;align-items:center;justify-content:center}
.dots{left:595px;top:513px;display:flex;gap:7px}
.dots span{width:12px;height:12px;border-radius:50%;background:var(--white);border:1px solid var(--white)}
.dots span.off{background:transparent;border-color:var(--white)}

/* section heads */
.sec-title{color:var(--green);font-size:26px;font-weight:500;letter-spacing:.5px}
.arrows{display:flex;gap:12px}
.arrows span{width:27px;height:27px;border-radius:50%;background:#8a8a8a;color:var(--white);display:flex;align-items:center;justify-content:center}

/* series cards */
.card-img{position:absolute;width:292px;height:239px;border-radius:10px;overflow:hidden}
.card-meta{position:absolute;width:292px;height:32px;display:flex;align-items:center}
.card-meta .av{width:30px;height:30px;border-radius:50%;margin-left:6px;margin-right:11px}
.card-meta .name{color:var(--green);font-weight:500;font-size:17px;flex:1;letter-spacing:.3px}
.card-meta svg{margin-left:14px}
.play{position:absolute;left:104px;top:64px;width:84px;height:84px;border-radius:50%;background:rgba(255,255,255,.85);display:flex;align-items:center;justify-content:center}
.controls{position:absolute;left:79px;top:198px;width:135px;height:41px;background:var(--green);display:flex}
.controls span{flex:1;display:flex;align-items:center;justify-content:center;border-right:1px solid rgba(255,255,255,.5)}

/* about */
.about-band{left:0;top:1389px;width:1200px;height:453px;background:var(--wash)}
.circle{position:absolute;border-radius:50%;background:var(--pale)}
.poster{left:782px;top:1352px;width:306px;height:449px;border-radius:10px;background:linear-gradient(180deg,#8c8c8c 0%,#3b3b3b 50%,#111 100%)}
.about-title{left:112px;top:1450px}
.about-text{left:112px;top:1494px;width:534px;font-size:16px;line-height:26.6px;color:var(--grey);text-align:justify}
.btn{position:absolute;top:1683px;height:56px;border-radius:9px;font-size:19px;font-weight:500;display:flex;align-items:center;justify-content:center}
.btn.solid{left:112px;width:249px;background:var(--green);color:var(--white)}
.btn.ghost{left:387px;width:254px;border:2px solid var(--mint);color:var(--green);background:var(--wash)}

/* blog */
.post{position:absolute;top:1985px;width:294px;height:370px;background:var(--white);border-radius:10px;box-shadow:0 3px 10px rgba(0,0,0,.12);overflow:hidden}
.post .img{height:227px}
.post .meta{display:flex;gap:28px;align-items:center;font-size:12px;color:var(--ink);padding:22px 0 0 13px}
.post .meta span{display:flex;align-items:center;gap:6px}
.post h3{font-size:16px;font-weight:500;color:var(--green);padding:8px 0 0 12px}
.post .by{display:flex;align-items:center;padding:12px 0 0 13px;font-size:16px;color:var(--grey)}
.post .by .av{width:34px;height:34px;border-radius:50%;margin-right:12px}
.post .by b{color:var(--green);font-weight:500;margin-left:6px}

/* footer */
.footer-shape{position:absolute;left:0;top:2440px;width:1200px;height:320px}
.f-brand{left:112px;top:2512px;color:var(--white);font-weight:600;font-size:33px;line-height:40px}
.f-about{left:112px;top:2615px;width:300px;color:var(--white);font-size:15.5px;line-height:23px}
.f-head{color:var(--white);font-size:24px;font-weight:500}
.f-links{left:536px;top:2555px;color:var(--white);font-size:16px;line-height:27.4px;list-style:none}
.f-contact{left:839px;top:2555px;color:var(--white);font-size:16px;width:260px}
.f-contact li{list-style:none;display:flex;gap:12px;line-height:26px;margin-bottom:16px}
.f-contact li svg{flex:none;margin-top:6px}
.copy{left:0;top:2776px;width:1200px;text-align:center;font-size:16px;color:var(--ink)}
</style>
</head>
<body>
<div class="page">

  <!-- Hero -->
  <div class="hero-photo" role="img" aria-label="Young woman with arms outstretched in warm sunset light"></div>
  <svg class="hero-shape" viewBox="0 0 620 570" aria-hidden="true"><polygon points="0,0 534,0 620,569 0,545" fill="var(--green)"/></svg>

  <div class="abs topmail">
    <svg width="18" height="14" viewBox="0 0 18 14"><rect x="1" y="1" width="16" height="12" rx="1.5" fill="none" stroke="#fff" stroke-width="1.6"/><path d="M1.5 2l7.5 6 7.5-6" fill="none" stroke="#fff" stroke-width="1.6"/></svg>
    hello@gatheredpath.org
  </div>
  <div class="abs socials"><span></span><span></span><span></span></div>

  <nav class="abs navbar">
    <div class="brand">GATHERED<br>PATH</div>
    <div class="menu">
      <a class="active">Home</a><a>About Us</a><a>video Bible studies</a><a>Blog</a><a>Contact</a>
    </div>
    <a class="signup">sign up</a>
  </nav>

  <div class="abs hero-title">
    <div class="lead">Welcome to</div>
    <div class="big">Christian&nbsp; Bible<br>study platform</div>
  </div>
  <a class="abs cta">GET STARTED</a>
  <div class="abs dots"><span></span><span class="off"></span><span></span></div>

  <!-- Series -->
  <h2 class="abs sec-title" style="left:111px;top:618px">OUR SERIES</h2>
  <div class="abs arrows" style="left:1012px;top:621px">
    <span><svg width="8" height="12" viewBox="0 0 8 12"><path d="M6 1L1 6l5 5" fill="none" stroke="#fff" stroke-width="1.6"/></svg></span>
    <span><svg width="8" height="12" viewBox="0 0 8 12"><path d="M2 1l5 5-5 5" fill="none" stroke="#fff" stroke-width="1.6"/></svg></span>
  </div>

  <div class="card-img" style="left:112px;top:678px;background:linear-gradient(160deg,#a9ad86,#6e7a55 50%,#2a2b33)" role="img" aria-label="Series speaker portrait outdoors"></div>
  <div class="card-img" style="left:453px;top:678px;background:linear-gradient(135deg,#3c3c3c,#1d1d1d)" role="img" aria-label="Video still for the God's Design series">
    <div class="play"><svg width="24" height="26" viewBox="0 0 24 26"><path d="M3 2l19 11L3 24z" fill="var(--green)"/></svg></div>
    <div class="controls">
      <span><svg width="18" height="16" viewBox="0 0 18 16"><path d="M2 5h4l5-4v14l-5-4H2z" fill="#fff"/><path d="M13 4a5 5 0 010 8" fill="none" stroke="#fff" stroke-width="1.6"/></svg></span>
      <span style="border:0"><svg width="18" height="18" viewBox="0 0 18 18"><path d="M3 11V9a6 6 0 0112 0v2" fill="none" stroke="#fff" stroke-width="1.8"/><rect x="2" y="10" width="4" height="6" rx="1" fill="#fff"/><rect x="12" y="10" width="4" height="6" rx="1" fill="#fff"/></svg></span>
    </div>
  </div>
  <div class="card-img" style="left:794px;top:678px;background:linear-gradient(160deg,#58613f,#8d8f74 45%,#d4887a)" role="img" aria-label="Smiling older speaker in a pink shirt"></div>

  <div class="card-img" style="left:112px;top:999px;background:linear-gradient(150deg,#6a6a5e,#8a8f93 50%,#4a4a50)" role="img" aria-label="Small group gathered around an open Bible"></div>
  <div class="card-img" style="left:453px;top:999px;background:linear-gradient(120deg,#4e5a6a,#2b2f36 55%,#9e3b3f)" role="img" aria-label="Hand holding a closed Bible"></div>
  <div class="card-img" style="left:794px;top:999px;background:linear-gradient(160deg,#d8d9d2,#5b6f83 50%,#6d8a45)" role="img" aria-label="Man praying on a park bench"></div>

  <!-- card meta rows -->
  <div class="card-meta" style="left:112px;top:931px"><span class="av" style="background:#b5896d"></span><span class="name">All THE THINGS</span>
    <svg width="26" height="24" viewBox="0 0 26 24"><path d="M13 2v13M8 10l5 5 5-5M2 14v7h22v-7" fill="none" stroke="#222" stroke-width="1.8"/></svg>
    <svg width="24" height="24" viewBox="0 0 24 24"><circle cx="5" cy="12" r="3" fill="none" stroke="#222" stroke-width="1.6"/><circle cx="19" cy="5" r="3" fill="none" stroke="#222" stroke-width="1.6"/><circle cx="19" cy="19" r="3" fill="none" stroke="#222" stroke-width="1.6"/><path d="M8 11l8-4M8 13l8 4" stroke="#222" stroke-width="1.6"/></svg></div>
  <div class="card-meta" style="left:453px;top:931px"><span class="av" style="background:#777"></span><span class="name">GOD'S DESIGN</span>
    <svg width="26" height="24" viewBox="0 0 26 24"><path d="M13 2v13M8 10l5 5 5-5M2 14v7h22v-7" fill="none" stroke="#222" stroke-width="1.8"/></svg>
    <svg width="24" height="24" viewBox="0 0 24 24"><circle cx="5" cy="12" r="3" fill="none" stroke="#222" stroke-width="1.6"/><circle cx="19" cy="5" r="3" fill="none" stroke="#222" stroke-width="1.6"/><circle cx="19" cy="19" r="3" fill="none" stroke="#222" stroke-width="1.6"/><path d="M8 11l8-4M8 13l8 4" stroke="#222" stroke-width="1.6"/></svg></div>
  <div class="card-meta" style="left:794px;top:931px"><span class="av" style="background:#c08d80"></span><span class="name">REVIVAL SERIES</span>
    <svg width="26" height="24" viewBox="0 0 26 24"><path d="M13 2v13M8 10l5 5 5-5M2 14v7h22v-7" fill="none" stroke="#222" stroke-width="1.8"/></svg>
    <svg width="24" height="24" viewBox="0 0 24 24"><circle cx="5" cy="12" r="3" fill="none" stroke="#222" stroke-width="1.6"/><circle cx="19" cy="5" r="3" fill="none" stroke="#222" stroke-width="1.6"/><circle cx="19" cy="19" r="3" fill="none" stroke="#222" stroke-width="1.6"/><path d="M8 11l8-4M8 13l8 4" stroke="#222" stroke-width="1.6"/></svg></div>
  <div class="card-meta" style="left:112px;top:1252px"><span class="av" style="background:#b5896d"></span><span class="name">JAMES</span>
    <svg width="26" height="24" viewBox="0 0 26 24"><path d="M13 2v13M8 10l5 5 5-5M2 14v7h22v-7" fill="none" stroke="#222" stroke-width="1.8"/></svg>
    <svg width="24" height="24" viewBox="0 0 24 24"><circle cx="5" cy="12" r="3" fill="none" stroke="#222" stroke-width="1.6"/><circle cx="19" cy="5" r="3" fill="none" stroke="#222" stroke-width="1.6"/><circle cx="19" cy="19" r="3" fill="none" stroke="#222" stroke-width="1.6"/><path d="M8 11l8-4M8 13l8 4" stroke="#222" stroke-width="1.6"/></svg></div>
  <div class="card-meta" style="left:453px;top:1252px"><span class="av" style="background:#8c6f78"></span><span class="name">PAUL'S LETTERS</span>
    <svg width="26" height="24" viewBox="0 0 26 24"><path d="M13 2v13M8 10l5 5 5-5M2 14v7h22v-7" fill="none" stroke="#222" stroke-width="1.8"/></svg>
    <svg width="24" height="24" viewBox="0 0 24 24"><circle cx="5" cy="12" r="3" fill="none" stroke="#222" stroke-width="1.6"/><circle cx="19" cy="5" r="3" fill="none" stroke="#222" stroke-width="1.6"/><circle cx="19" cy="19" r="3" fill="none" stroke="#222" stroke-width="1.6"/><path d="M8 11l8-4M8 13l8 4" stroke="#222" stroke-width="1.6"/></svg></div>
  <div class="card-meta" style="left:794px;top:1252px"><span class="av" style="background:#3a2f2a"></span><span class="name">OTHER LETTERS</span>
    <svg width="26" height="24" viewBox="0 0 26 24"><path d="M13 2v13M8 10l5 5 5-5M2 14v7h22v-7" fill="none" stroke="#222" stroke-width="1.8"/></svg>
    <svg width="24" height="24" viewBox="0 0 24 24"><circle cx="5" cy="12" r="3" fill="none" stroke="#222" stroke-width="1.6"/><circle cx="19" cy="5" r="3" fill="none" stroke="#222" stroke-width="1.6"/><circle cx="19" cy="19" r="3" fill="none" stroke="#222" stroke-width="1.6"/><path d="M8 11l8-4M8 13l8 4" stroke="#222" stroke-width="1.6"/></svg></div>

  <!-- About -->
  <div class="abs about-band"></div>
  <div class="circle" style="left:999px;top:1382px;width:168px;height:168px"></div>
  <div class="circle" style="left:672px;top:1656px;width:200px;height:200px"></div>
  <div class="abs poster" role="img" aria-label="Series cover: speaker portrait in black and white with series title"></div>

  <h2 class="abs sec-title about-title">ABOUT US</h2>
  <p class="abs about-text">Lorem ipsum dolor sit amet, consectetur adipiscing elit, sed do eiusmod tempor incididunt ut labore et dolore magna aliqua. Ut enim ad minim veniam, quis nostrud exercitation ullamco laboris nisi ut aliquip ex ea commodo consequat. Duis aute irure dolor in reprehenderit in voluptate velit esse cillum dolore eu fugiat nulla pariatur.</p>
  <a class="btn solid">Topical Studies</a>
  <a class="btn ghost">Doctrinal Studies</a>

  <!-- Blog -->
  <h2 class="abs sec-title" style="left:109px;top:1912px">BLOG</h2>
  <div class="abs arrows" style="left:1012px;top:1916px">
    <span><svg width="8" height="12" viewBox="0 0 8 12"><path d="M6 1L1 6l5 5" fill="none" stroke="#fff" stroke-width="1.6"/></svg></span>
    <span><svg width="8" height="12" viewBox="0 0 8 12"><path d="M2 1l5 5-5 5" fill="none" stroke="#fff" stroke-width="1.6"/></svg></span>
  </div>

  <article class="post" style="left:112px">
    <div class="img" role="img" aria-label="Hands joined in prayer around a wooden table" style="background:linear-gradient(140deg,#5a4334,#8b6a52 50%,#3b2c22)"></div>
    <div class="meta"><span><svg width="10" height="14" viewBox="0 0 10 14"><path d="M5 0v14M1 4h8" stroke="#222" stroke-width="1.6"/></svg>Church Pastor</span><span><svg width="12" height="12" viewBox="0 0 12 12"><rect x="1" y="2" width="10" height="9" fill="none" stroke="#222"/><path d="M1 5h10" stroke="#222"/></svg>Jan&nbsp; 20, 2021</span></div>
    <h3>Expecting new Love issued cases</h3>
    <div class="by"><span class="av" style="background:#c2907a"></span>By<b>Nora Ellwood</b></div>
  </article>
  <article class="post" style="left:452px">
    <div class="img" role="img" aria-label="Folded hands resting on an open Bible" style="background:linear-gradient(140deg,#9ea4b4,#d7c3c2 50%,#7a2d33)"></div>
    <div class="meta"><span><svg width="10" height="14" viewBox="0 0 10 14"><path d="M5 0v14M1 4h8" stroke="#222" stroke-width="1.6"/></svg>Church Pastor</span><span><svg width="12" height="12" viewBox="0 0 12 12"><rect x="1" y="2" width="10" height="9" fill="none" stroke="#222"/><path d="M1 5h10" stroke="#222"/></svg>Jan&nbsp; 20, 2021</span></div>
    <h3>Expecting new Love issued cases</h3>
    <div class="by"><span class="av" style="background:#8d7a6a"></span>By<b>Darien Holt</b></div>
  </article>
  <article class="post" style="left:791px">
    <div class="img" role="img" aria-label="Open Bible held above a wooden table" style="background:linear-gradient(180deg,#cfcac4,#b47a50 55%,#a4582b)"></div>
    <div class="meta"><span><svg width="10" height="14" viewBox="0 0 10 14"><path d="M5 0v14M1 4h8" stroke="#222" stroke-width="1.6"/></svg>Church Pastor</span><span><svg width="12" height="12" viewBox="0 0 12 12"><rect x="1" y="2" width="10" height="9" fill="none" stroke="#222"/><path d="M1 5h10" stroke="#222"/></svg>Jan&nbsp; 20, 2021</span></div>
    <h3>Expecting new Love issued cases</h3>
    <div class="by"><span class="av" style="background:#3d3d48"></span>By<b>Walt Brenner</b></div>
  </article>

  <!-- Footer -->
  <svg class="footer-shape" viewBox="0 0 1200 320" aria-hidden="true"><polygon points="0,24 585,0 1200,24 1200,320 0,320" fill="var(--teal)"/></svg>
  <div class="abs f-brand">GATHERED<br>PATH</div>
  <p class="abs f-about">Nulla quis lorem ut libero malesuada feugiat. Quisque velit nisi, pretium ut lacinia in</p>

  <h4 class="abs f-head" style="left:535px;top:2497px">Information</h4>
  <ul class="abs f-links"><li>Home</li><li>About Us</li><li>video Bible studies</li><li>Blog</li><li>Contact</li></ul>

  <h4 class="abs f-head" style="left:839px;top:2495px">Contact</h4>
  <ul class="abs f-contact">
    <li><svg width="12" height="16" viewBox="0 0 12 16"><path d="M6 15s5-6 5-9.5A5 5 0 001 5.5C1 9 6 15 6 15z" fill="#fff"/><circle cx="6" cy="5.5" r="1.8" fill="var(--teal)"/></svg><span>Lorem ipsum dolor sit amet, consectetur adipiscing elit, sed.</span></li>
    <li><svg width="14" height="14" viewBox="0 0 14 14"><path d="M3 1l3 3-1.5 2a8 8 0 003.5 3.5L10 8l3 3-2 2C6 13 1 8 1 3z" fill="#fff"/></svg><span>+1 07933 410265</span></li>
    <li><svg width="16" height="12" viewBox="0 0 16 12"><rect x="1" y="1" width="14" height="10" fill="none" stroke="#fff" stroke-width="1.4"/><path d="M1 1l7 5 7-5" fill="none" stroke="#fff" stroke-width="1.4"/></svg><span>hello@gatheredpath.org</span></li>
  </ul>

  <p class="abs copy">© Copyright 2022 gatheredpath.org. All Rights Reserved.</p>
</div>
</body>
</html>
```